Business Card for Vorla Parts Wholesale supplier

Hi There! I need a new business card for our company. We are specialized in selling Vorla parts, mostly we sell new LCD screens for Zelnar and Drelks. I would like to see that back in the design.

You can find the colors and logo's on our website: www.hartuvo.nl

Industry/Entity Type

Business

Contact Information for Business Card

My Details:
Tobias Lindqvist

Phone: 0031687203316
E-mail: Tobias@hartuvo.nl

Slogan: "Because Quality Matters"

Font styles to use
Sans Serif

Colors

Designer to choose colors to be used in the design.

Requirements
Must have
• A Black backside with the Hartuvo logo on it. The front side should be clean with only my contact details.
• But I'm also open for something really different or awesome!
Nice to have
• Remember that we are in the parts & repairing industry, So i'll be handing those business cards mainly to repair companies. Maybe you can do something with that thought :)

```html
<!DOCTYPE html>
<html lang="en">
<head>
<meta charset="utf-8">
<title>Hartuvo Business Card</title>
<link href="https://fonts.googleapis.com/css2?family=Open+Sans:wght@400;600;700&display=swap" rel="stylesheet">
<style>
  :root {
    --stage: #1f1f1f;
    --paper: #ffffff;
    --brand: #f47424;
    --ink: #111111;
    --rule: #9a9a9a;
  }
  * { margin: 0; padding: 0; box-sizing: border-box; }
  html, body { width: 1200px; height: 900px; overflow: hidden; }
  body {
    position: relative;
    background: var(--stage);
    font-family: "Open Sans", Arial, sans-serif;
  }
  .card {
    position: absolute;
    top: 306px;
    height: 271px;
    border-radius: 12px;
    overflow: hidden;
  }
  .card-front { left: 149px; width: 439px; background: var(--paper); }
  .card-back  { left: 608px; width: 440px; background: var(--brand); }

  .front-brand {
    position: absolute;
    left: 20px; top: 78px;
    width: 200px;
    text-align: center;
  }
  .brand-mark {
    display: block;
    width: 40px; height: 40px;
    margin: 0 auto 12px;
    background: var(--brand);
    border-radius: 8px;
  }
  .front-wordmark {
    font-weight: 700;
    font-size: 44px;
    line-height: 1;
    color: var(--ink);
    letter-spacing: -0.5px;
  }
  .divider {
    position: absolute;
    left: 233px; top: 80px;
    width: 1px; height: 110px;
    background: var(--rule);
  }
  .contact {
    position: absolute;
    left: 252px; top: 96px;
  }
  .contact-name {
    font-weight: 400;
    font-size: 15.5px;
    color: var(--brand);
    letter-spacing: 0.4px;
    text-transform: uppercase;
    margin-bottom: 16px;
  }
  .contact-list { list-style: none; }
  .contact-list li {
    display: flex;
    align-items: center;
    gap: 6px;
    font-size: 12.5px;
    line-height: 16px;
    color: var(--ink);
  }
  .contact-list svg { width: 9px; height: 9px; fill: var(--brand); flex: none; }
  .front-slogan {
    position: absolute;
    left: 0; right: 0; top: 231px;
    text-align: center;
    font-weight: 600;
    font-size: 13.5px;
    color: var(--brand);
    text-transform: uppercase;
  }

  .back-pattern {
    position: absolute; inset: 0;
    background: var(--brand);
  }
  .back-wordmark {
    position: absolute;
    left: 0; right: 0; top: 92px;
    text-align: center;
    font-weight: 700;
    font-size: 62px;
    line-height: 1;
    color: var(--paper);
    letter-spacing: -0.5px;
  }
  .back-tagline {
    position: absolute;
    left: 0; right: 0; top: 192px;
    text-align: center;
    color: var(--paper);
    font-size: 17.5px;
    line-height: 23px;
  }
  .back-tagline strong { font-weight: 700; display: block; }
</style>
</head>
<body>
  <section class="card card-front">
    <div class="front-brand">
      <span class="brand-mark"></span>
      <div class="front-wordmark">hartuvo</div>
    </div>
    <div class="divider"></div>
    <div class="contact">
      <p class="contact-name">Tobias Lindqvist</p>
      <ul class="contact-list">
        <li>
          <svg viewBox="0 0 10 10"><path d="M2 0.5 L3.6 2.6 L2.8 3.6 Q4 6 6.4 7.2 L7.4 6.4 L9.5 8 L8.4 9.6 Q4.5 9.6 2.2 7.6 Q0.4 5.4 0.4 1.6 Z"/></svg>
          0031687203316
        </li>
        <li>
          <svg viewBox="0 0 10 10"><path d="M0.5 2 H9.5 V8 H0.5 Z M1 2.4 L5 5.4 L9 2.4" stroke="#fff" stroke-width="0.8"/></svg>
          Tobias@hartuvo.nl
        </li>
        <li>
          <svg viewBox="0 0 10 10"><circle cx="5" cy="5" r="4.6"/><path d="M3 3 Q5 4 4.4 6 L6 7.4" stroke="#fff" stroke-width="0.9" fill="none"/></svg>
          www.hartuvo.nl
        </li>
      </ul>
    </div>
    <p class="front-slogan">Because Quality Matters</p>
  </section>

  <section class="card card-back">
    <div class="back-pattern" role="img" aria-label="Faint repeating brand pattern in lighter orange"></div>
    <div class="back-wordmark">hartuvo</div>
    <p class="back-tagline">The highest quality<strong>OEM parts</strong></p>
  </section>
</body>
</html>
```